Custom Cabinet Shop Needs a website design

Hi,
We need a website for a Custom Cabinet Shop and Cabinet parts manufacturing business.
The business has two sides to it. One side provides custom Kitchens, vanities, entertainment units, offices and what not to homeowners and contractors.
The 2nd side of the business provides built to order cabinet boxes and other parts required to put together a project to other cabinet shops, small contractors looking to install there own cabinets.
Website will need a Gallery to display work.
Color scheme to go well with logo.
current website is www.brambleoakcustomcabinets.com
being changed to www.brambleoak.ca
Logo Included in attached files.
Tagline "Joinery with Spirit"
Mission Statement "Our passion is to deliver inspired cabinetry solutions to suit all your needs, supported by our phenomenal star class customer service"
The website should convey quality and professionalism.
Thank you.
Homeowners/ Contractors
Entertainment

```html
<!DOCTYPE html>
<html lang="en">
<head>
<meta charset="utf-8">
<title>Brambleoak Custom Cabinets</title>
<link rel="stylesheet" href="https://fonts.googleapis.com/css2?family=Roboto+Condensed:wght@300;400;700&family=Open+Sans:wght@300;400;600&family=Montserrat:wght@800&display=swap">
<style>
:root{
  --orange:#f15a24;
  --ink:#222;
  --text:#333;
  --muted:#777;
  --cream:#f4f2ec;
  --footer:#161616;
  --white:#fff;
}
*{margin:0;padding:0;box-sizing:border-box}
html,body{width:941px;height:1200px;overflow:hidden;background:var(--white)}
body{position:relative;font-family:"Open Sans",sans-serif;color:var(--text)}
.abs{position:absolute}
.top-rule{left:0;top:0;width:941px;height:3px;background:var(--orange)}
.brand{left:86px;top:34px;display:flex;align-items:center;gap:10px}
.brand-mark{width:34px;height:34px;border-radius:50%;background:var(--orange)}
.brand-name{font-family:"Roboto Condensed",sans-serif;font-weight:700;font-size:26px;color:var(--ink);letter-spacing:.5px}
.util-links{right:86px;top:13px;display:flex;gap:20px;font-size:8px;font-weight:600;color:#555}
.util-links span::before{content:"";display:inline-block;width:8px;height:8px;border-radius:2px;background:#444;margin-right:5px;vertical-align:-1px}
.call{right:86px;top:38px;font-family:"Roboto Condensed",sans-serif;font-size:23px;color:var(--ink)}
.call em{font-style:normal;color:var(--orange)}
.nav{right:86px;top:76px;display:flex;gap:38px;font-family:"Roboto Condensed",sans-serif;font-size:15px;color:#333}
.nav .active{color:var(--orange);position:relative}
.nav .active::after{content:"";position:absolute;left:-5px;right:-6px;top:26px;height:3px;background:var(--orange)}
.hero-band{left:0;top:108px;width:941px;height:358px;background:linear-gradient(#e4e0da,#d8d2ca);border-bottom:1px solid #ccc}
.hero-band::before{content:"";position:absolute;inset:10px 0;background:linear-gradient(90deg,#d9d0c4,#ebe6df 30%,#ebe6df 70%,#e6dfd5)}
.hero-photo{left:86px;top:122px;width:769px;height:330px;background:linear-gradient(160deg,#3a3a3e 0%,#5a4432 45%,#8a6442 62%,#2e2a28 100%)}
.arrow{top:250px;width:28px;height:75px;display:flex;align-items:center;justify-content:center}
.arrow.prev{left:59px;background:#2a2a2a}
.arrow.next{left:855px;background:var(--orange)}
.hero-title{left:517px;top:350px;width:338px;height:43px;background:rgba(0,0,0,.85);color:var(--white);font-family:"Roboto Condensed",sans-serif;font-weight:300;font-size:31px;line-height:43px;text-align:right;padding-right:16px;letter-spacing:-.5px}
.hero-title b{font-weight:700}
.hero-sub{left:630px;top:393px;width:225px;height:25px;background:var(--orange);color:var(--white);font-family:"Roboto Condensed",sans-serif;font-weight:700;font-size:15px;line-height:25px;text-align:right;padding-right:18px}
.res-photo{left:86px;top:505px;width:297px;height:197px;background:linear-gradient(135deg,#c9c2b6 0%,#7a5034 45%,#a06a3e 70%,#3a2a22 100%)}
.res-title{left:394px;top:502px;font-size:28px;font-weight:400;color:var(--ink)}
.res-text{left:395px;top:539px;width:462px;font-size:11.2px;line-height:14.2px;font-weight:300;color:#222}
.res-text p+p{margin-top:14px}
.btn{left:396px;top:649px;width:94px;height:30px;background:var(--orange);color:var(--white);font-family:"Roboto Condensed",sans-serif;font-size:12px;line-height:30px;text-align:center}
.gallery-band{left:0;top:740px;width:941px;height:302px;background:var(--cream)}
.gal-title{left:86px;top:760px;font-size:22px;font-weight:400;color:var(--ink)}
.gal-title span{color:var(--orange);font-weight:600}
.gal-rule{left:86px;top:793px;width:769px;height:1px;background:#d6d3cc}
.gal-rule-accent{left:86px;top:792px;width:36px;height:3px;background:var(--orange)}
.gal-ctrl{left:831px;top:770px}
.card{top:821px;width:177px;height:183px;overflow:hidden}
.card .shot{position:absolute;inset:0}
.card .cap{position:absolute;left:0;bottom:0;width:100%;height:35px;background:rgba(30,30,30,.85);color:var(--white);font-size:14px;line-height:35px;padding-left:15px}
.card.open .cap{height:97px;background:#262626;text-align:center;padding:38px 10px 0;line-height:1.3}
.card.open .cap small{display:block;font-size:9.5px;color:#bbb;margin-top:6px;font-weight:300}
.plus{left:148px;top:886px;width:52px;height:52px;border-radius:50%;background:var(--orange);display:flex;align-items:center;justify-content:center}
.footer{left:0;top:1042px;width:941px;height:158px;background:var(--footer)}
.foot-nav{left:0;top:1073px;width:941px;display:flex;justify-content:center;gap:31px;font-size:12px;color:var(--white)}
.foot-nav .active{font-weight:600}
.social{left:0;top:1110px;width:941px;display:flex;justify-content:center;gap:6px}
.social span{width:23px;height:23px;border-radius:50%;background:var(--white)}
.copy{left:0;top:1155px;width:941px;text-align:center;font-size:9.5px;color:var(--white)}
</style>
</head>
<body>
<div class="abs top-rule"></div>
<header>
  <div class="abs brand"><span class="brand-mark"></span><span class="brand-name">BRAMBLEOAK</span></div>
  <div class="abs util-links"><span>My Favorites</span><span>Brambleoak.com</span><span>For Dealers</span></div>
  <div class="abs call"><em>Call Us</em> : 403-555-0187</div>
  <nav class="abs nav"><span class="active">Home</span><span>Our Gallery</span><span>Our Services</span><span>Warranty</span><span>Contact Us</span></nav>
</header>

<section>
  <div class="abs hero-band"></div>
  <div class="abs hero-photo" role="img" aria-label="Basement bar with live-edge wood counter, stone base, stools and pendant lights"></div>
  <div class="abs arrow prev"><svg width="8" height="14" viewBox="0 0 8 14"><path d="M7 1 1 7l6 6" fill="none" stroke="#fff" stroke-width="1.6"/></svg></div>
  <div class="abs arrow next"><svg width="8" height="14" viewBox="0 0 8 14"><path d="M1 1l6 6-6 6" fill="none" stroke="#fff" stroke-width="1.6"/></svg></div>
  <div class="abs hero-title">JOINERY WITH <b>SPIRIT</b></div>
  <div class="abs hero-sub">custom cabinet design company</div>
</section>

<section>
  <div class="abs res-photo" role="img" aria-label="Kitchen with wood cabinets and a live-edge dining counter set for a meal"></div>
  <h2 class="abs res-title">Residential</h2>
  <div class="abs res-text">
    <p>Here at Brambleoak Custom Cabinets we are proud to be involved in the custom cabinet market. By employing and partnering up with local artisans we are able to deliver a product that is second to none.</p>
    <p>With our 3D Screen-to-Machine software you can see first hand exactly what you will be getting before a single piece is cut.</p>
  </div>
  <div class="abs btn">Reade More</div>
</section>

<section>
  <div class="abs gallery-band"></div>
  <h2 class="abs gal-title">Our <span>Gallery</span></h2>
  <div class="abs gal-rule"></div>
  <div class="abs gal-rule-accent"></div>
  <svg class="abs gal-ctrl" width="24" height="14" viewBox="0 0 24 14"><path d="M9 1 3 7l6 6M15 1l6 6-6 6" fill="none" stroke="#bbb" stroke-width="1.5"/></svg>

  <div class="abs card open" style="left:87px">
    <div class="shot" role="img" aria-label="Kitchen with honey wood cabinets and dark island" style="background:linear-gradient(135deg,#e0d4c0,#9a6a3e 50%,#5a3a22)"></div>
    <div class="cap">Consectetur Adipisicing<small>Adipisicing elit eiusmod tempor incididunt ut labore magna.</small></div>
  </div>
  <div class="abs card" style="left:284px">
    <div class="shot" role="img" aria-label="White kitchen with steel appliances and stone backsplash" style="background:linear-gradient(135deg,#f2efe8,#d8cfc0 50%,#8a8278)"></div>
    <div class="cap">Consectetur Adipisicing</div>
  </div>
  <div class="abs card" style="left:481px">
    <div class="shot" role="img" aria-label="Kitchen with cherry cabinets and granite island" style="background:linear-gradient(135deg,#e8e2d8,#8a3a24 50%,#5a2216)"></div>
    <div class="cap">Consectetur Adipisicing</div>
  </div>
  <div class="abs card" style="left:678px">
    <div class="shot" role="img" aria-label="Open kitchen with wood island and pendant lights" style="background:linear-gradient(135deg,#f0ece6,#a87a56 50%,#6a4a34)"></div>
    <div class="cap">Consectetur Adipisicing</div>
  </div>
  <div class="abs plus"><svg width="28" height="28" viewBox="0 0 28 28"><path d="M14 3v22M3 14h22" stroke="#fff" stroke-width="5"/></svg></div>
</section>

<footer>
  <div class="abs footer"></div>
  <nav class="abs foot-nav"><span class="active">Home</span><span>Our Gallery</span><span>Our Services</span><span>Warranty</span><span>Contact Us</span></nav>
  <div class="abs social" aria-label="Social links"><span></span><span></span><span></span><span></span><span></span><span></span></div>
  <p class="abs copy">Copyrights © 2015. Brambleoak Custom Cabinets . All Rights Reserved</p>
</footer>
</body>
</html>
```